RW Framewell Inc Business cards

We need business cards using our existing logo but slightly modified. Right now the logo says RW Loadbearing Masonry. We want to keep the RW part of the design, but replace the Structural Concrete portion with "FRAMEWELL". Please see the attached file.
Ideally this would be a blank template so we can add Different Names, titles, and phone numbers later.
On the one side we want only the logo and on the other side the detail. I'm attaching an example for you to see.
Please reach out with any other questions. Our address and other details will be given out once we find a design we like.

Target Market(s)

Construction Industry

```html
<!DOCTYPE html>
<html lang="en">
<head>
<meta charset="utf-8">
<title>RW Framewell Inc Business Cards</title>
<link href="https://fonts.googleapis.com/css2?family=Michroma&family=Arimo:wght@400;700&display=swap" rel="stylesheet">
<style>
  :root {
    --stage: #2f2f30;
    --brand-blue: #1f74bd;
    --brand-blue-light: #2b82c8;
    --paper: #ffffff;
    --paper-shade: #ececec;
    --ink-grey: #7a7a7c;
    --rule-grey: #d4d4d4;
  }
  * { margin: 0; padding: 0; box-sizing: border-box; }
  html, body {
    width: 1200px; height: 866px; overflow: hidden;
    background: var(--stage);
  }
  .sheet {
    width: 1200px; height: 866px;
    display: flex; flex-direction: column; align-items: center; justify-content: center;
    gap: 44px;
  }
  .card {
    position: relative;
    width: 640px; height: 366px;
    overflow: hidden;
    box-shadow: 0 10px 24px rgba(0,0,0,0.45);
  }
  /* Front: logo only */
  .card--front {
    background: linear-gradient(135deg, var(--brand-blue) 0%, var(--brand-blue-light) 55%, var(--brand-blue) 100%);
    display: flex; align-items: center; justify-content: center;
  }
  .wordmark {
    display: flex; align-items: center; gap: 18px;
    font-family: "Michroma", sans-serif;
    font-weight: 400;
    letter-spacing: 2px;
  }
  .wordmark__square { width: 26px; height: 26px; }
  .card--front .wordmark { color: var(--paper); font-size: 40px; }
  .card--front .wordmark__square { background: var(--paper); }

  /* Back: details */
  .card--back {
    background: linear-gradient(160deg, var(--paper) 0%, var(--paper) 45%, var(--paper-shade) 100%);
  }
  .contact {
    position: absolute; left: 44px; top: 110px;
  }
  .contact__name {
    font-family: "Michroma", sans-serif;
    font-size: 19px; color: var(--brand-blue); letter-spacing: 1px;
  }
  .contact__title {
    font-family: "Arimo", sans-serif;
    font-size: 15px; color: var(--ink-grey); margin-top: 4px;
  }
  .contact__list { list-style: none; margin-top: 16px; }
  .contact__item {
    display: flex; align-items: center; gap: 10px;
    font-family: "Arimo", sans-serif;
    font-size: 15px; color: var(--ink-grey); line-height: 22px;
  }
  .contact__icon { width: 16px; height: 14px; flex: none; }
  .card--back .wordmark {
    position: absolute; right: 44px; top: 128px;
    color: var(--brand-blue); font-size: 28px;
  }
  .card--back .wordmark__square { width: 20px; height: 20px; background: var(--brand-blue); }
  .rule {
    position: absolute; left: 44px; right: 44px; top: 262px;
    height: 1px; background: var(--rule-grey);
  }
  .website {
    position: absolute; right: 44px; top: 284px;
    font-family: "Arimo", sans-serif; font-size: 16px;
    color: var(--ink-grey); letter-spacing: 0.5px;
  }
  .website__domain { color: var(--brand-blue); }
</style>
</head>
<body>
  <main class="sheet">
    <section class="card card--front" aria-label="Card front">
      <div class="wordmark">
        <span class="wordmark__square"></span>
        <span class="wordmark__text">RW FRAMEWELL</span>
      </div>
    </section>

    <section class="card card--back" aria-label="Card back">
      <div class="contact">
        <h1 class="contact__name">DANIEL HARTLEY</h1>
        <p class="contact__title">Managing Director</p>
        <ul class="contact__list">
          <li class="contact__item">
            <svg class="contact__icon" viewBox="0 0 16 14" aria-hidden="true">
              <rect x="0.75" y="0.75" width="14.5" height="12.5" rx="2" fill="none" stroke="#1f74bd" stroke-width="1.5"/>
              <path d="M6 3.5 C4.6 4.5 4.6 9.5 6 10.5 L7.5 9.2 L6.8 7.8 L6.8 6.2 L7.5 4.8 Z" fill="#1f74bd"/>
            </svg>
            055-274 318 906
          </li>
          <li class="contact__item">
            <svg class="contact__icon" viewBox="0 0 16 14" aria-hidden="true">
              <rect x="0.5" y="2" width="15" height="10" fill="#1f74bd"/>
              <path d="M0.5 2 L8 8 L15.5 2" fill="none" stroke="#ffffff" stroke-width="1.2"/>
            </svg>
            office@framewell-mail.com
          </li>
        </ul>
      </div>

      <div class="wordmark">
        <span class="wordmark__square"></span>
        <span class="wordmark__text">RW FRAMEWELL</span>
      </div>

      <div class="rule"></div>
      <p class="website">www.<span class="website__domain">framewellbuild</span>.com</p>
    </section>
  </main>
</body>
</html>
```